Commercial Real Estate

We need a business card design for a new commercial real estate business that specializes in apartment building brokerage. Not individual units but the entire complex. We find and represent the owners existing buildings and well as new buyers for those buildings. The design should convey trust, integrity, knowledge and growth. It should be easily read.

Target Market(s)

40 to 65 years old

Industry/Entity Type

Real Estate

```html
<!DOCTYPE html>
<html lang="en">
<head>
<meta charset="utf-8">
<title>Crestline Property Investments – Business Card</title>
<link rel="stylesheet" href="https://fonts.googleapis.com/css2?family=Lato:wght@400;700;900&display=swap">
<style>
  :root {
    --teal: #5ec4c0;
    --slate: #3f5654;
    --ink: #2f3e3d;
    --paper: #fbfbfb;
    --backdrop: #2a2a2a;
  }
  * { box-sizing: border-box; margin: 0; padding: 0; }
  html, body {
    width: 1200px; height: 900px; overflow: hidden;
    background: var(--backdrop);
    font-family: "Lato", sans-serif;
  }
  .card {
    position: absolute; left: 75px; top: 150px;
    width: 1050px; height: 600px;
    background: var(--paper);
    overflow: hidden;
  }
  .name-tag {
    position: absolute; right: 0; top: 44px;
    width: 330px; height: 48px;
    background: var(--teal);
    border-radius: 24px 0 0 24px;
    color: #fff; font-weight: 900; font-size: 30px;
    line-height: 48px; padding-left: 28px; letter-spacing: 0.5px;
  }
  .designation {
    position: absolute; right: 168px; top: 98px;
    color: var(--ink); font-size: 17px; font-weight: 700; letter-spacing: 0.5px;
  }
  .brand {
    position: absolute; left: 70px; top: 360px; width: 420px;
  }
  .brand-name {
    display: flex; align-items: center; gap: 16px;
    color: var(--slate); font-weight: 900; font-size: 58px; letter-spacing: 2px;
  }
  .brand-dot { width: 26px; height: 26px; border-radius: 50%; background: var(--teal); flex: none; }
  .brand-rule { height: 3px; background: var(--teal); margin: 10px 0 10px; }
  .brand-tagline {
    color: var(--slate); font-weight: 900; font-size: 22px; letter-spacing: 6px;
  }
  .contact {
    position: absolute; left: 520px; top: 190px;
    color: var(--ink); font-size: 22px;
  }
  .address { color: var(--teal); font-weight: 900; font-size: 22px; line-height: 1.35; margin-bottom: 22px; }
  .contact-line { display: flex; align-items: center; gap: 14px; margin-bottom: 14px; }
  .contact-line svg { width: 24px; height: 20px; flex: none; }
  .website { font-weight: 900; font-size: 24px; margin-top: 12px; }
  .website span { color: var(--teal); }
  .skyline {
    position: absolute; left: 560px; top: 400px;
    width: 490px; height: 110px;
    background: var(--slate);
  }
  .service-band {
    position: absolute; right: 0; top: 505px;
    width: 500px; height: 50px;
    background: var(--teal);
    border-radius: 25px 0 0 25px;
    color: #fff; font-weight: 900; font-size: 24px;
    line-height: 50px; padding-left: 26px; letter-spacing: 0.5px;
  }
</style>
</head>
<body>
  <main class="card">
    <div class="name-tag">YOUR NAME</div>
    <div class="designation">DESIGNATION</div>

    <section class="brand">
      <div class="brand-name"><span class="brand-dot"></span>CRESTLINE</div>
      <div class="brand-rule"></div>
      <div class="brand-tagline">Property Investments</div>
    </section>

    <section class="contact">
      <p class="address">12 Rue Verlaine,<br>94200 Ivry sur Seine</p>
      <p class="contact-line">
        <svg viewBox="0 0 24 20" aria-hidden="true"><rect x="4" y="8" width="16" height="11" rx="2" fill="var(--teal)"/><path d="M1 7c3-6 19-6 22 0l-3 2c-2-3-14-3-16 0z" fill="var(--teal)"/><circle cx="12" cy="13.5" r="2.5" fill="#fff"/></svg>
        +33 (0)6 41 52 63 70
      </p>
      <p class="contact-line">
        <svg viewBox="0 0 24 20" aria-hidden="true"><rect x="1" y="2" width="22" height="16" fill="var(--teal)"/><path d="M1 2l11 9 11-9" fill="none" stroke="#fff" stroke-width="1.8"/></svg>
        Info@crestlineinvest.com
      </p>
      <p class="website">www.<span>crestlineinvest</span>.com</p>
    </section>

    <div class="skyline" role="img" aria-label="City skyline silhouette of apartment towers"></div>
    <div class="service-band">APARTMENT BUILDING BROKERAGE</div>
  </main>
</body>
</html>
```